Caldrift - Where every box finds its place!

Hello,
I'd like to update, re-vamp, and re-tool this current power point presentation with slightly more professional appearance as well as more accurately reflect the website -caldrift.com- color scheme and sleek design scheme. Please see attached.
We at Caldrift pride ourselves on seeking to rework an archaic business into something progressive, cost effective, more reliable, and easily accessible in todays fast growing market that has only gotten more expensive, more costly and less indirect over the last couple years.

Target Market(s)

New updated and hassle free moving opportunities no matter how large or how small in a market that begs for a change

Industry/Entity Type

Logistics/Moving

Requirements
Must have
• The current color scheme from the -caldrift.com- website as well as the inclusion of the current data on the sample power point presentation provided but with updated graphics

```html
<!DOCTYPE html>
<html lang="en">
<head>
<meta charset="utf-8">
<title>Caldrift – Presentation Deck</title>
<link rel="stylesheet" href="https://fonts.googleapis.com/css2?family=Mulish:wght@300;400;600;700;800;900&display=swap">
<style>
:root{
  --blue:#2f6ee5;
  --blue-deep:#2a5fd0;
  --gold:#e6c35c;
  --yellow:#fbcd5f;
  --navy:#0c1a2d;
  --navy-line:#10233c;
  --ink:#333a45;
  --grey:#5a6170;
  --card:#f3f4f8;
  --sheet:#dcdde0;
  --white:#ffffff;
}
*{box-sizing:border-box;margin:0;padding:0}
html,body{width:840px;height:1200px;overflow:hidden}
body{background:var(--sheet);font-family:'Mulish',sans-serif;color:var(--ink);position:relative}
.slide{position:absolute;width:727px;height:409px;background:var(--white);overflow:hidden;transform:scale(.5224);transform-origin:0 0}
.col-left{left:26px}.col-right{left:428px}
.row-1{top:34px}.row-2{top:268px}.row-3{top:497px}.row-4{top:726px}.row-5{top:953px}
.abs{position:absolute}
.brand{position:absolute;display:flex;align-items:center;gap:10px;font-weight:800;color:var(--blue);letter-spacing:1px;line-height:1}
.brand::before{content:"";display:block;width:.6em;height:.6em;background:var(--gold)}
.divider{position:absolute;width:2px;background:var(--gold)}
.heading{position:absolute;color:var(--blue);font-weight:800;letter-spacing:.5px;line-height:1}
.url{position:absolute;font-size:12px;color:var(--ink);letter-spacing:.3px}
.url-rule{position:absolute;height:1.5px;background:var(--gold)}
.photo{position:absolute}
.center{text-align:center}

/* title */
.title-main{position:absolute;left:33px;top:128px;font-size:44px;font-weight:300;color:var(--blue);line-height:51px}

/* about */
.about-copy{position:absolute;left:402px;top:78px;width:272px;font-size:12.4px;line-height:19.7px;color:var(--ink)}
.about-copy p+p{margin-top:19px}

/* vision */
.pillar{position:absolute;top:116px;width:200px;text-align:center}
.pillar-icon{width:74px;height:74px;border-radius:50%;background:var(--gold);margin:0 auto;display:flex;align-items:center;justify-content:center}
.pillar h3{margin-top:20px;font-size:16px;font-weight:800;color:var(--blue)}
.pillar .lead{margin-top:9px;font-size:11.2px;line-height:13.5px;color:var(--blue)}
.pillar .body{margin-top:12px;font-size:8.4px;line-height:10.2px;color:var(--grey)}

/* solution */
.solution-banner{position:absolute;left:13px;top:72px;width:279px;height:125px;background:var(--blue);color:var(--white);font-size:17px;font-weight:300;line-height:21px;display:flex;align-items:center;justify-content:center;text-align:center}
.feature{position:absolute;top:205px;width:136px;height:183px;background:var(--card);text-align:center;padding:18px 8px 0}
.feature svg{display:block;margin:0 auto}
.feature h4{margin-top:10px;font-size:11px;font-weight:800;color:var(--blue-deep)}
.feature p{margin-top:7px;font-size:7.6px;line-height:10.2px;color:var(--grey)}

/* questions */
.questions{position:absolute;left:27px;top:312px;font-size:31px;font-weight:900;color:var(--blue);line-height:38px}

/* problems */
.cell{position:absolute;width:157px;height:141px;overflow:hidden}
.cell.fill{background:var(--yellow)}
.cell.open{background:var(--white);border:2px solid var(--navy-line);text-align:center;padding:26px 10px 0}
.cell.open h4{font-size:14px;font-weight:800;color:var(--blue-deep)}
.cell.open p{margin-top:8px;font-size:8.4px;line-height:13.4px;color:var(--ink)}
.cell .num{position:absolute;left:6px;top:2px;font-size:38px;font-weight:900;color:#f2bd45;line-height:1}
.cell svg{position:absolute;left:38px;top:40px}

/* accomplished */
.goal-card{position:absolute;width:198px;height:106px;background:var(--white);box-shadow:0 3px 12px rgba(20,40,80,.1);display:flex;align-items:center;justify-content:center;text-align:center;font-size:13.5px;line-height:19px;color:var(--ink);padding-top:10px}
.goal-card.gold{border-top:4px solid var(--yellow)}
.goal-card.blue{border-top:4px solid var(--blue)}
.goal-num{position:absolute;width:52px;height:52px;border-radius:50%;display:flex;align-items:center;justify-content:center;font-size:14px;font-weight:800}
.goal-num.gold{background:var(--yellow);color:var(--navy)}
.goal-num.blue{background:var(--blue);color:var(--white)}

/* promise */
.promise-band{position:absolute;left:0;top:77px;width:727px;height:332px;background:var(--navy)}
.promise-item{position:absolute;color:var(--white)}
.promise-item .ico{width:28px;height:28px;border-radius:50%;border:2px solid var(--blue);background:var(--white);display:flex;align-items:center;justify-content:center;margin-bottom:11px}
.promise-item h4{font-size:11.4px;font-weight:800;line-height:13px;letter-spacing:.2px}
.promise-item p{margin-top:6px;font-size:8.6px;line-height:10.6px;color:#dfe4ee}

/* services */
.service-band{position:absolute;left:0;top:128px;width:727px;height:281px;background:var(--blue)}
.service-frame{position:absolute;top:76px;width:224px;height:160px;background:var(--yellow);padding:5px 5px 0}
.service-frame .photo{position:static;width:100%;height:100%}
.service{position:absolute;top:250px;width:224px;text-align:center;color:var(--white)}
.service h4{font-size:13px;font-weight:800;letter-spacing:.3px}
.service p{margin-top:9px;font-size:10.6px;line-height:14.4px}

/* thanks */
.contact-panel{position:absolute;left:322px;top:0;width:405px;height:409px;background:linear-gradient(180deg,#3572e6,#2c66dc)}
.contact{position:absolute;left:86px;display:flex;align-items:center;gap:20px;color:var(--white);font-size:13.5px;line-height:17px;letter-spacing:.3px}
.contact .dot{width:40px;height:40px;border-radius:50%;background:var(--gold);display:flex;align-items:center;justify-content:center;flex:none}
.thanks{position:absolute;left:57px;top:193px;font-size:32px;font-weight:900;color:var(--blue);letter-spacing:.5px}
</style>
</head>
<body>

<!-- Title -->
<section class="slide col-left row-1">
  <div class="brand" style="left:35px;top:42px;font-size:34px">Caldrift</div>
  <h1 class="title-main">Moving for<br>the next<br>generation</h1>
  <div class="url-rule" style="left:35px;top:350px;width:113px"></div>
  <div class="url" style="left:35px;top:361px;font-size:13px">www.caldrift.com</div>
  <div class="photo" role="img" aria-label="Smiling family carrying cardboard moving boxes outdoors" style="left:298px;top:0;width:429px;height:409px;background:linear-gradient(135deg,#9aa36f,#c9a07a 45%,#b98a5e 70%,#6f7a4e)"></div>
</section>

<!-- About -->
<section class="slide col-right row-1">
  <div class="brand" style="left:17px;top:20px;font-size:26px">Caldrift</div>
  <div class="divider" style="left:207px;top:16px;height:38px"></div>
  <h2 class="heading" style="left:234px;top:25px;font-size:22px">ABOUT US</h2>
  <div class="photo" role="img" aria-label="Family unpacking boxes in a bright new living room" style="left:0;top:65px;width:362px;height:344px;background:linear-gradient(160deg,#e7e3dc,#c9a882 55%,#b89370)"></div>
  <div class="abs" style="left:362px;top:58px;width:8px;height:351px;background:var(--blue)"></div>
  <div class="abs" style="left:355px;top:58px;width:7px;height:6px;background:var(--gold)"></div>
  <div class="about-copy">
    <p>Caldrift is the next logical evolution in professional moving. Professional moving clients have battled soaring prices, acute capacity problems and deteriorating service levels.</p>
    <p>Caldrift was founded by lifelong moving professionals who have developed the answer to better moving services. Poised as THE industry disruptor, we deliver faster, offer guaranteed prices and even offer no credit check financing options. We are a technology first organization using proprietary software to deliver moving's best service experience.</p>
  </div>
  <div class="url-rule" style="left:602px;top:383px;width:115px"></div>
  <div class="url" style="right:9px;top:388px;font-size:12.5px">www.caldrift.com</div>
</section>

<!-- Vision -->
<section class="slide col-left row-2">
  <div class="brand" style="left:20px;top:28px;font-size:26px">Caldrift</div>
  <div class="divider" style="left:207px;top:16px;height:55px"></div>
  <h2 class="heading" style="left:233px;top:16px;font-size:21px">CALDRIFT VISION</h2>
  <div class="abs" style="left:233px;top:42px;width:330px;font-size:11.8px;line-height:14px;color:var(--ink)">The traditional moving industry is broken, outdated, inefficient,and unable to change.</div>

  <div class="pillar" style="left:13px">
    <div class="pillar-icon"><svg width="36" height="22" viewBox="0 0 36 22"><path d="M2 11C8 2 28 2 34 11C28 20 8 20 2 11Z" fill="#fff"/><circle cx="18" cy="11" r="6" fill="#e6c35c"/><circle cx="18" cy="11" r="3" fill="#fff"/></svg></div>
    <h3>Our Vision</h3>
    <p class="lead">Revolutionize an $86B industry by providing great value to everyone involved</p>
    <p class="body">Caldrift Customers - Consumers, Movers, Corporate Clients, and Relocation Management Companies all receive better value with Caldrift than anywhere else</p>
  </div>
  <div class="divider" style="left:245px;top:118px;height:247px"></div>
  <div class="pillar" style="left:262px">
    <div class="pillar-icon"><svg width="34" height="30" viewBox="0 0 34 30"><path d="M2 29L17 6L32 29Z" fill="#fff"/><path d="M17 1V8" stroke="#fff" stroke-width="2"/><path d="M17 1H25L23 4L25 7H17Z" fill="#fff"/></svg></div>
    <h3>Our Mission</h3>
    <p class="lead">Disrupt a sleepy giant of an inefficient industry</p>
    <p class="body">Caldrift's deep understanding of the professional moving industry, supported by extensive market research has set Caldrift up for ultimate success in disrupting this industry by creating cost-saving efficiencies throughout.</p>
  </div>
  <div class="divider" style="left:498px;top:118px;height:247px"></div>
  <div class="pillar" style="left:512px">
    <div class="pillar-icon"><svg width="34" height="34" viewBox="0 0 34 34"><circle cx="16" cy="18" r="13" fill="none" stroke="#fff" stroke-width="4"/><circle cx="16" cy="18" r="5" fill="#fff"/><path d="M16 18L30 4" stroke="#fff" stroke-width="3"/></svg></div>
    <h3>Our Goal</h3>
    <p class="lead">Becoming the moving platform of choice</p>
    <p class="body">As Caldrift's market share grows, the customer acquisition cost and operational cost plummets. This creates even more market penetration, more efficiencies, and exponential growth.</p>
  </div>
  <div class="url-rule" style="left:602px;top:382px;width:114px"></div>
  <div class="url" style="right:10px;top:388px;font-size:12.5px">www.caldrift.com</div>
</section>

<!-- Solution -->
<section class="slide col-right row-2">
  <div class="brand" style="left:20px;top:24px;font-size:26px">Caldrift</div>
  <div class="divider" style="left:207px;top:16px;height:48px"></div>
  <h2 class="heading" style="left:233px;top:26px;font-size:21px">SOLUTION</h2>
  <div class="solution-banner">Bringing the Customer<br>Experience to the<br>21st Century</div>
  <div class="photo" role="img" aria-label="Presenter speaking to a seated audience in a brick-walled room" style="left:298px;top:72px;width:419px;height:125px;background:linear-gradient(90deg,#6e4a36,#b08a6e 40%,#d8d2c8 75%,#efece6)"></div>

  <div class="feature" style="left:12px">
    <svg width="36" height="32" viewBox="0 0 36 32"><rect x="2" y="3" width="26" height="20" fill="none" stroke="#2f6ee5" stroke-width="2"/><path d="M8 28H22M15 23V28" stroke="#2f6ee5" stroke-width="2"/><circle cx="27" cy="20" r="6" fill="#fff" stroke="#2f6ee5" stroke-width="2"/><circle cx="27" cy="20" r="2" fill="#2f6ee5"/><path d="M7 10H20M7 15H17" stroke="#2f6ee5" stroke-width="2"/></svg>
    <h4>Ridorized Process</h4>
    <p>Caldrift automatically audits: Compliance, Insurance, Regulatory, Bonding, Background checks, and Quality.</p>
  </div>
  <div class="feature" style="left:155px">
    <svg width="34" height="34" viewBox="0 0 34 34"><circle cx="17" cy="17" r="16" fill="#2f6ee5"/><path d="M12 9C12 9 10 10 10 13C10 18 15 24 21 25C24 25 25 23 25 23L22 20L20 21C18 20 15 17 14 15L15 13Z" fill="#fff"/></svg>
    <h4>One Point of Contact</h4>
    <p>Today moves are sold from broker to broker until it's finally sold to a mover. Many entities involved means a confusing line of correspondence for the customer.</p>
  </div>
  <div class="feature" style="left:298px">
    <svg width="34" height="34" viewBox="0 0 34 34"><rect x="2" y="4" width="20" height="6" rx="1" fill="none" stroke="#2f6ee5" stroke-width="2"/><rect x="2" y="13" width="16" height="6" rx="1" fill="none" stroke="#2f6ee5" stroke-width="2"/><circle cx="23" cy="22" r="10" fill="#fff" stroke="#2f6ee5" stroke-width="2.5"/><text x="23" y="27" font-size="13" font-weight="800" text-anchor="middle" fill="#2f6ee5" font-family="Mulish,sans-serif">$</text></svg>
    <h4>Book Now Pay Later</h4>
    <p>Moving has a high price tag, but no one has ever offered a pay later solution. Much less a no credit check offer.</p>
  </div>
  <div class="feature" style="left:441px">
    <svg width="34" height="34" viewBox="0 0 34 34"><circle cx="17" cy="17" r="11" fill="none" stroke="#2f6ee5" stroke-width="3"/><circle cx="17" cy="17" r="5" fill="#2f6ee5"/><path d="M17 1V7M17 27V33M1 17H7M27 17H33" stroke="#2f6ee5" stroke-width="3"/></svg>
    <h4>GPS Tracking</h4>
    <p>Parcelwise has conditioned consumers to expect real-time tracking of goods. Only Caldrift enables you to track all of your belongings door to door.</p>
  </div>
  <div class="feature" style="left:584px">
    <svg width="34" height="34" viewBox="0 0 34 34"><path d="M3 11L17 3L31 11Z" fill="#2f6ee5"/><path d="M7 14V27M13 14V27M21 14V27M27 14V27" stroke="#2f6ee5" stroke-width="3"/><rect x="3" y="29" width="28" height="3" fill="#2f6ee5"/></svg>
    <h4>Simple Honest Pricing</h4>
    <p>Caldrift's proprietary algorithms and data are backed up by a checks and balances process giving the first instant pricing solution that won't change.</p>
  </div>
  <div class="url" style="right:9px;top:394px;font-size:9px">www.caldrift.com</div>
</section>

<!-- Questions -->
<section class="slide col-left row-3">
  <div class="photo" role="img" aria-label="Couple laughing while pushing a moving box across a sunny living room floor" style="left:0;top:0;width:727px;height:409px;background:linear-gradient(120deg,#f3eee6,#e6ddd0 40%,#cdb59a 65%,#e9e3da)"></div>
  <div class="brand" style="left:28px;top:277px;font-size:26px">Caldrift</div>
  <h2 class="questions">DO YOU HAVE<br>ANY QUESTIONS?</h2>
  <div class="url" style="right:8px;top:394px;font-size:8.5px">www.caldrift.com</div>
</section>

<!-- Problems -->
<section class="slide col-right row-3">
  <div class="brand" style="left:50px;top:33px;font-size:26px">Caldrift</div>
  <div class="divider" style="left:228px;top:20px;height:54px"></div>
  <h2 class="heading" style="left:247px;top:37px;font-size:21px">MOVING'S PROBLEMS</h2>

  <div class="cell fill" style="left:49px;top:93px"><span class="num">01</span>
    <svg width="80" height="74" viewBox="0 0 80 74"><path d="M14 10H34L30 18C44 26 46 56 38 68H8C0 56 2 26 16 18Z" fill="#0c1a2d"/><text x="23" y="55" font-size="26" font-weight="900" text-anchor="middle" fill="#fbcd5f" font-family="Mulish,sans-serif">$</text><rect x="42" y="30" width="34" height="7" rx="3.5" fill="#0c1a2d"/><rect x="42" y="41" width="34" height="7" rx="3.5" fill="#0c1a2d"/><rect x="42" y="52" width="34" height="7" rx="3.5" fill="#0c1a2d"/><rect x="42" y="63" width="34" height="7" rx="3.5" fill="#0c1a2d"/></svg>
  </div>
  <div class="cell open" style="left:206px;top:93px"><h4>CAPACITY</h4><p>Long-haul driver shortages and limited equipment coupled with growing demand has pushed capacity to a crisis state</p></div>
  <div class="cell fill" style="left:363px;top:93px"><span class="num">03</span>
    <svg width="80" height="74" viewBox="0 0 80 74"><path d="M18 38C18 18 62 18 62 38" fill="none" stroke="#0c1a2d" stroke-width="6"/><rect x="12" y="34" width="12" height="20" rx="4" fill="#0c1a2d"/><rect x="56" y="34" width="12" height="20" rx="4" fill="#0c1a2d"/><path d="M62 54C62 62 52 66 44 66" fill="none" stroke="#0c1a2d" stroke-width="4"/><rect x="36" y="62" width="10" height="8" rx="3" fill="#0c1a2d"/></svg>
  </div>
  <div class="cell open" style="left:520px;top:93px"><h4>TRANSPARANCY</h4><p>Too many margin layers...van line, agent, driver and help. In addition, charges are convoluted and confusing</p></div>

  <div class="cell open" style="left:49px;top:234px"><h4>COST</h4><p>Moving cost has skyrocketed over the last three years. Charges have increased 38% since 2018.</p></div>
  <div class="cell fill" style="left:206px;top:234px"><span class="num">02</span>
    <svg width="90" height="74" viewBox="0 0 90 74"><rect x="2" y="10" width="52" height="44" fill="#0c1a2d"/><path d="M58 24H74L86 40V56H58Z" fill="#0c1a2d"/><rect x="64" y="29" width="10" height="10" fill="#fbcd5f"/><circle cx="18" cy="60" r="9" fill="#0c1a2d" stroke="#fbcd5f" stroke-width="3"/><circle cx="72" cy="60" r="9" fill="#0c1a2d" stroke="#fbcd5f" stroke-width="3"/></svg>
  </div>
  <div class="cell open" style="left:363px;top:234px"><h4>SERVICE</h4><p>Quality labor has been difficult to source and afford. Virtually all RMC's report a decline in service quality</p></div>
  <div class="cell fill" style="left:520px;top:234px"><span class="num">04</span>
    <svg width="80" height="80" viewBox="0 0 80 80"><circle cx="48" cy="30" r="26" fill="#0c1a2d"/><path d="M32 30C38 20 58 20 64 30C58 40 38 40 32 30Z" fill="#fbcd5f"/><circle cx="48" cy="30" r="6" fill="#0c1a2d"/><path d="M30 50L8 72" stroke="#0c1a2d" stroke-width="9" stroke-linecap="round"/></svg>
  </div>
  <svg class="abs" style="left:0;top:0" width="727" height="409" viewBox="0 0 727 409">
    <path d="M122 233L127 240L132 233Z" fill="#fbcd5f"/><path d="M280 236L285 229L290 236Z" fill="#fbcd5f"/><path d="M436 233L441 240L446 233Z" fill="#fbcd5f"/><path d="M594 236L599 229L604 236Z" fill="#fbcd5f"/>
  </svg>
</section>

<!-- Accomplished -->
<section class="slide col-left row-4">
  <div class="photo" role="img" aria-label="Faded background of movers carrying boxes" style="left:0;top:0;width:727px;height:409px;background:linear-gradient(135deg,#fbfaf7,#f4efe6 50%,#f8f5f0)"></div>
  <div class="brand" style="left:30px;top:25px;font-size:26px">Caldrift</div>
  <div class="divider" style="left:211px;top:18px;height:36px"></div>
  <h2 class="heading" style="left:228px;top:27px;font-size:21px">WHAT CALDRIFT HAS ACCOMPLISHED</h2>

  <div class="goal-card gold" style="left:38px;top:110px">Eliminate Capacity<br>Constraints</div>
  <div class="goal-num gold" style="left:113px;top:80px">01</div>
  <div class="goal-card blue" style="left:262px;top:110px">Reduce Costs</div>
  <div class="goal-num blue" style="left:335px;top:80px">02</div>
  <div class="goal-card gold" style="left:485px;top:110px">Improve Service<br>Levels</div>
  <div class="goal-num gold" style="left:559px;top:80px">03</div>

  <div class="goal-card blue" style="left:150px;top:262px">Simplify the<br>Moving Process</div>
  <div class="goal-num blue" style="left:223px;top:232px">04</div>
  <div class="goal-card gold" style="left:373px;top:262px">Break the Typical<br>Moving Mold</div>
  <div class="goal-num gold" style="left:447px;top:232px">05</div>
</section>

<!-- Promise / map -->
<section class="slide col-right row-4">
  <div class="brand" style="left:20px;top:26px;font-size:26px">Caldrift</div>
  <div class="divider" style="left:202px;top:18px;height:42px"></div>
  <div class="abs" style="left:220px;top:20px;font-size:13px;color:var(--ink)">Peace Of Mind, Every Step Of The Way</div>
  <h2 class="heading" style="left:220px;top:40px;font-size:17.5px">TRANSPARENT STRESS FREE MOVING</h2>
  <div class="promise-band"></div>
  <div class="photo" role="img" aria-label="Map of the United States marked with service location pins" style="left:172px;top:128px;width:350px;height:210px;border-radius:20px;background:radial-gradient(ellipse at center,#1f3452,#0c1a2d 72%)"></div>

  <div class="promise-item" style="left:20px;top:102px;width:150px">
    <div class="ico"><svg width="14" height="14" viewBox="0 0 14 14"><rect x="2" y="1" width="10" height="12" fill="none" stroke="#2f6ee5" stroke-width="1.6"/><path d="M4 5H10M4 8H10M4 11H8" stroke="#2f6ee5" stroke-width="1.4"/></svg></div>
    <h4>INDEPENDENT<br>INVENTORY SURVEY</h4>
    <p>Video-recorded inventory surveys allow you to rest easy knowing everything has been accounted for. No disputes or unpleasant surprises after the move.</p>
  </div>
  <div class="promise-item" style="left:20px;top:270px;width:170px">
    <div class="ico"><svg width="14" height="14" viewBox="0 0 14 14"><path d="M7 1L12 3V7C12 10 7 13 7 13C7 13 2 10 2 7V3Z" fill="none" stroke="#2f6ee5" stroke-width="1.6"/></svg></div>
    <h4>MOVE PROTECTION</h4>
    <p>Extra coverage for your belongings, no matter how they're transported, helps you relax and enjoy your move worry-free.</p>
  </div>
  <div class="promise-item" style="left:542px;top:110px;width:160px">
    <div class="ico"><svg width="14" height="14" viewBox="0 0 14 14"><path d="M7 13C7 13 2 8 2 5A5 5 0 0 1 12 5C12 8 7 13 7 13Z" fill="#2f6ee5"/><circle cx="7" cy="5" r="1.8" fill="#fff"/></svg></div>
    <h4>SHIPMENT TRACKING</h4>
    <p>Enjoy peace of mind, knowing you can track your items at all times during the move from any device.</p>
  </div>
  <div class="promise-item" style="left:542px;top:254px;width:160px">
    <div class="ico"><svg width="14" height="14" viewBox="0 0 14 14"><rect x="2" y="4" width="10" height="9" fill="none" stroke="#2f6ee5" stroke-width="1.6"/><path d="M2 7H12M7 4V13" stroke="#2f6ee5" stroke-width="1.4"/></svg></div>
    <h4>SPECIAL SERVICES</h4>
    <p>Are there items that need special care or unique customizations to your move? We have special services to fit your move.</p>
  </div>
</section>

<!-- Services -->
<section class="slide col-left row-5">
  <div class="brand" style="left:20px;top:26px;font-size:26px">Caldrift</div>
  <div class="divider" style="left:203px;top:16px;height:45px"></div>
  <div class="abs" style="left:219px;top:18px;font-size:13px;color:var(--ink)">Caldrift Services</div>
  <h2 class="heading" style="left:219px;top:39px;font-size:17.5px">WHAT CAN WE HELP YOU WITH?</h2>
  <div class="service-band"></div>

  <div class="service-frame" style="left:15px"><div class="photo" role="img" aria-label="Couple carrying boxes through a bright home entrance" style="background:linear-gradient(150deg,#f0ede8,#cfc1ae 55%,#8d7a63)"></div></div>
  <div class="service-frame" style="left:252px"><div class="photo" role="img" aria-label="Team packing boxes in a corporate office meeting room" style="background:linear-gradient(150deg,#cfd2d4,#5a5d60 50%,#b6a893)"></div></div>
  <div class="service-frame" style="left:488px"><div class="photo" role="img" aria-label="Open-plan office floor stacked with moving boxes" style="background:linear-gradient(170deg,#e4e6e8,#c2c6ca 55%,#c9ab85)"></div></div>

  <div class="service" style="left:15px"><h4>RESIDENTIAL MOVES</h4><p>Whether you're moving to a new apartment or home, Caldrift makes it easy. Our comprehensive services and flexible payment options offer peace of mind during your relocation.</p></div>
  <div class="service" style="left:252px"><h4>CORPORATE MOVES</h4><p>Our processes are structured around delivering the best results within flexible relocation packages, from lump sum to reimbursement to full relocation packages. Our API, operational systems, and data access allow relocation managers full insight to optimize their programs.</p></div>
  <div class="service" style="left:488px"><h4>OFFICE MOVES</h4><p>We understand the importance of ensuring business continuity during an office move. Our team of expert movers can help you quickly and efficiently relocate your office to its new location while minimizing downtime.</p></div>
  <div class="url-rule" style="left:622px;top:388px;width:95px;background:#fff"></div>
  <div class="url" style="right:10px;top:393px;font-size:9px;color:#fff">www.caldrift.com</div>
</section>

<!-- Thank you -->
<section class="slide col-right row-5">
  <div class="brand" style="left:58px;top:108px;font-size:26px">Caldrift</div>
  <div class="url-rule" style="left:57px;top:180px;width:205px;height:3px"></div>
  <h2 class="thanks">THANK YOU!</h2>
  <div class="url-rule" style="left:57px;top:246px;width:205px;height:3px"></div>
  <div class="contact-panel">
    <div class="contact" style="top:112px"><span class="dot"><svg width="16" height="20" viewBox="0 0 16 20"><path d="M8 19C8 19 1 11 1 7A7 7 0 0 1 15 7C15 11 8 19 8 19Z" fill="#2f6ee5"/><circle cx="8" cy="7" r="2.5" fill="#e6c35c"/></svg></span><span>412 HARLOW AVENUE<br>BROOKVALE, TX 75501</span></div>
    <div class="contact" style="top:187px"><span class="dot"><svg width="18" height="18" viewBox="0 0 18 18"><path d="M4 1C4 1 1 2 1 5C1 11 7 17 13 17C16 17 17 14 17 14L13 11L11 13C9 12 6 9 5 7L7 5Z" fill="#2f6ee5"/></svg></span><span>(800) 555-0147</span></div>
    <div class="contact" style="top:265px"><span class="dot"><svg width="18" height="16" viewBox="0 0 18 16"><path d="M1 6L9 1L17 6V15H1Z" fill="#2f6ee5"/><path d="M1 6L9 11L17 6" fill="none" stroke="#e6c35c" stroke-width="1.5"/></svg></span><span>CALDRIFT.COM<br>SUPPORT@CALDRIFT.COM</span></div>
  </div>
</section>

</body>
</html>
```